Custom Cabinet Shop Needs a website design

Hi,
We need a website for a Custom Cabinet Shop and Cabinet parts manufacturing business.
The business has two sides to it. One side provides custom Kitchens, vanities, entertainment units, offices and what not to homeowners and contractors.
The 2nd side of the business provides built to order cabinet boxes and other parts required to put together a project to other cabinet shops, small contractors looking to install there own cabinets.
Website will need a Gallery to display work.
Color scheme to go well with logo.
current website is www.brambleoakcustomcabinets.com
being changed to www.brambleoak.ca
Logo Included in attached files.
Tagline "Joinery with Spirit"
Mission Statement "Our passion is to deliver inspired cabinetry solutions to suit all your needs, supported by our phenomenal star class customer service"
The website should convey quality and professionalism.
Thank you.
Homeowners/ Contractors
Entertainment

```html
<!DOCTYPE html>
<html lang="en">
<head>
<meta charset="utf-8">
<title>Bramble Oak Custom Cabinets</title>
<link rel="stylesheet" href="https://fonts.googleapis.com/css2?family=Great+Vibes&family=Dancing+Script:wght@600&family=Quicksand:wght@500;600&display=swap">
<style>
:root{
  --band:#cbbcb0;
  --nav:#cfbfb3;
  --white:#ffffff;
  --accent:#e8733a;
  --wood-light:#f2b27a;
  --wood-mid:#e9a064;
  --wood-dark:#d98b4e;
  --brown:#7a3412;
  --brown-soft:#8f4a26;
  --ink:#3a2e28;
  --field:#c9a99b;
}
*{margin:0;padding:0;box-sizing:border-box}
html,body{width:1200px;height:2833px;overflow:hidden}
body{position:relative;font-family:"Quicksand",sans-serif;background:var(--white);color:var(--ink)}
.abs{position:absolute}
.nav{left:0;top:0;width:1200px;height:63px;background:var(--nav)}
.brand{left:162px;top:14px;display:flex;align-items:center;gap:10px;color:var(--ink);font-weight:600;font-size:17px;letter-spacing:1px}
.brand-dot{width:30px;height:30px;border-radius:50%;background:var(--accent)}
.nav-links{right:200px;top:24px;display:flex;gap:52px;list-style:none;font-size:11px;font-weight:600;color:var(--white);letter-spacing:1px}
.nav-links .active{color:var(--accent)}
.hero{left:0;top:63px;width:1200px;height:609px;background:radial-gradient(ellipse at 45% 60%,#8a4a22 0%,#4a2a18 45%,#1c1a24 100%)}
.tagline{left:0;top:270px;width:1200px;text-align:center;font-family:"Great Vibes",cursive;font-size:78px;line-height:95px;color:var(--white)}
.cta{left:512px;top:512px;width:178px;height:40px;border:2px solid var(--white);color:var(--white);font-size:19px;display:flex;align-items:center;justify-content:center}
.band{left:0;width:1200px;background:var(--band)}
.band-label{position:absolute;left:162px;font-family:"Dancing Script",cursive;font-size:27px;color:var(--white)}
.band-notch{position:absolute;left:200px;bottom:-12px;width:0;height:0;border-left:12px solid transparent;border-right:12px solid transparent;border-top:12px solid var(--band)}
.about{left:0;top:735px;width:1200px;height:633px;background:linear-gradient(180deg,#e9dcb0 0%,#c7a36a 35%,#5a3a24 70%,#3a2a20 100%)}
.mission{left:0;top:1050px;width:1200px;text-align:center;color:var(--white);font-size:27px;line-height:29px;font-weight:600;letter-spacing:.5px}
.services{left:0;top:1437px;width:1200px;height:415px;background:linear-gradient(90deg,var(--wood-mid),var(--wood-light) 40%,var(--wood-mid) 70%,var(--wood-dark))}
.service{width:280px;text-align:center;top:1510px;color:var(--brown)}
.service svg{display:block;margin:0 auto}
.service h3{font-family:"Dancing Script",cursive;font-size:30px;font-weight:600;margin-top:38px}
.service p{font-size:14px;font-weight:600;line-height:25px;margin-top:10px;color:var(--brown-soft)}
.gallery-item{top:1915px;height:540px}
.arrow{top:2121px;width:55px;height:53px;background:#e6cfc4;display:flex;align-items:center;justify-content:center}
.signup{left:0;top:2526px;width:1200px;height:136px;background:var(--white)}
.signup-text{left:0;top:2544px;width:1200px;text-align:center;font-size:15px;font-weight:600;color:var(--ink)}
.field{left:342px;top:2583px;width:385px;height:36px;border:2px solid var(--field);font-size:13px;color:var(--field);padding:8px 14px}
.submit{left:739px;top:2583px;width:113px;height:36px;border:2px solid var(--field);font-size:13px;color:var(--field);display:flex;align-items:center;justify-content:center}
.footer{left:0;top:2662px;width:1200px;height:171px;background:linear-gradient(90deg,var(--wood-mid),var(--wood-light) 50%,var(--wood-dark))}
.footer-brand{left:0;top:2704px;width:1200px;display:flex;justify-content:center;align-items:center;gap:8px;color:var(--brown);font-weight:600;font-size:17px}
.footer-brand .brand-dot{width:22px;height:22px;background:var(--brown)}
.social{left:0;top:2754px;width:1200px;display:flex;justify-content:center;gap:14px}
.social span{width:14px;height:14px;border-radius:50%;background:var(--brown)}
.copy{left:0;top:2786px;width:1200px;text-align:center;font-size:10px;color:var(--brown);font-weight:600}
</style>
</head>
<body>
<header class="abs nav"></header>
<div class="abs brand"><span class="brand-dot"></span>Bramble Oak</div>
<ul class="abs nav-links"><li class="active">HOME</li><li>ABOUT</li><li>SERVICES</li><li>GALLERY</li><li>CONTACT</li></ul>

<section class="abs hero" role="img" aria-label="Photo of a custom kitchen bar with live-edge counter, stools and pendant lights"></section>
<h1 class="abs tagline">"Joinery with<br>Spirit"</h1>
<div class="abs cta">Contact us</div>

<div class="abs band" style="top:672px;height:63px"><span class="band-label" style="top:10px">A little About us</span><span class="band-notch"></span></div>
<section class="abs about" role="img" aria-label="Photo of a sunlit dining nook with rustic wood table, bench seat and cushions"></section>
<p class="abs mission">“Our passion is to deliver inspired cabinetry solutions<br>to suit all your needs, supported by<br>our phenomenal star class customer service.”</p>

<div class="abs band" style="top:1368px;height:69px"><span class="band-label" style="top:12px">Services</span><span class="band-notch"></span></div>
<section class="abs services" aria-label="Services"></section>
<div class="abs service" style="left:180px">
  <svg width="120" height="120" viewBox="0 0 120 120" fill="none" stroke="#7a3412" stroke-width="3"><circle cx="60" cy="60" r="57"/><path d="M38 60 L60 40 L82 60 M44 56 V80 H76 V56 M55 80 V66 H65 V80"/></svg>
  <h3>Residential</h3><p>Donec id elit non mi porta<br>gravida at eget metus,</p>
</div>
<div class="abs service" style="left:457px">
  <svg width="120" height="120" viewBox="0 0 120 120" fill="none" stroke="#7a3412" stroke-width="3"><circle cx="60" cy="60" r="57"/><circle cx="60" cy="54" r="16"/><path d="M52 54 L58 60 L68 48 M50 68 L44 84 L52 80 L56 86 L60 72 M70 68 L76 84 L68 80 L64 86 L60 72"/></svg>
  <h3>Limited Warranty</h3><p>Donec id elit non mi porta<br>gravida at eget metus,</p>
</div>
<div class="abs service" style="left:732px">
  <svg width="120" height="120" viewBox="0 0 120 120" fill="none" stroke="#7a3412" stroke-width="3"><circle cx="60" cy="60" r="57"/><path d="M38 44 H82 L86 54 H34 Z M38 54 V80 H82 V54 M48 80 V64 H72 V80"/></svg>
  <h3>Business</h3><p>Donec id elit non mi porta<br>gravida at eget metus,</p>
</div>

<div class="abs band" style="top:1852px;height:63px"><span class="band-label" style="top:10px">Our Gallery</span><span class="band-notch"></span></div>
<div class="abs gallery-item" style="left:0;width:336px;background:linear-gradient(180deg,#8a8680,#2a2420 60%,#6a6660)" role="img" aria-label="Photo of a dark wall unit with stone-clad bar"></div>
<div class="abs gallery-item" style="left:344px;width:510px;background:linear-gradient(180deg,#d8d0c4,#b8aea0 45%,#3a2e28)" role="img" aria-label="Photo of a white kitchen with stainless appliances and granite island"></div>
<div class="abs gallery-item" style="left:862px;width:338px;background:linear-gradient(180deg,#5a4a40,#e8e4dc 45%,#6a3a20)" role="img" aria-label="Photo of white cabinets and a two-tone island"></div>
<div class="abs arrow" style="left:263px"><svg width="14" height="18" viewBox="0 0 14 18"><path d="M10 3 L4 9 L10 15" stroke="#fff" stroke-width="3" fill="none"/></svg></div>
<div class="abs arrow" style="left:888px"><svg width="14" height="18" viewBox="0 0 14 18"><path d="M4 3 L10 9 L4 15" stroke="#fff" stroke-width="3" fill="none"/></svg></div>

<div class="abs band" style="top:2455px;height:71px"><span class="band-label" style="top:14px">Get in touch</span><span class="band-notch"></span></div>
<section class="abs signup" aria-label="Newsletter"></section>
<p class="abs signup-text">Sign up now for more information about</p>
<div class="abs field">Enter your e-mail</div>
<div class="abs submit">Contact</div>

<footer class="abs footer"></footer>
<div class="abs footer-brand"><span class="brand-dot"></span>Bramble Oak</div>
<div class="abs social"><span></span><span></span><span></span><span></span><span></span></div>
<p class="abs copy">© 2015 Bramble Oak Custom Cabinets. All rights reserved.</p>
</body>
</html>
```